Business card design needed

I would like a one sided black business card with the information provided above. Refer to my website www.brightvolleyracquets.com.au for an example of colors I have used for my site, would like to keep this consistent for my business cards also, I will upload my logo below.

I am a new small business that provides tennis customers with racquet re stringing, tennis strings and accessories.

Industry/Entity Type

Small Business

Contact Information for Business Card

Bright Volley Tennis

Owen Whitby
Managing Director

brightvolleyracquets@mailbox.example
www.brightvolleyracquets.com.au
0491 726 305

Racquet Restringing/Tennis Strings/Accessories

Requirements
Must have
• Must have my logo and card must be black

```html
<!DOCTYPE html>
<html lang="en">
<head>
<meta charset="utf-8">
<title>Bright Volley Tennis – Business Card</title>
<link rel="stylesheet" href="https://fonts.googleapis.com/css2?family=PT+Sans:wght@400;700&display=swap">
<style>
  :root {
    --bg: #e9e7e4;
    --card: #000000;
    --band: #1f4f7e;
    --lime: #b5d334;
    --white: #ffffff;
    --font: "PT Sans", "Myriad Pro", Arial, sans-serif;
  }
  html, body {
    margin: 0;
    padding: 0;
    width: 1200px;
    height: 750px;
    overflow: hidden;
    background: var(--bg);
    font-family: var(--font);
  }
  .canvas {
    position: relative;
    width: 1200px;
    height: 750px;
  }
  .card {
    position: absolute;
    left: 75px;
    top: 75px;
    width: 1050px;
    height: 598px;
    background: var(--card);
    border-radius: 40px;
    overflow: hidden;
  }
  .brand {
    position: absolute;
    left: 0;
    top: 130px;
    width: 930px;
    display: flex;
    justify-content: center;
    align-items: center;
    gap: 18px;
  }
  .brand-dot {
    width: 34px;
    height: 34px;
    border-radius: 50%;
    background: var(--lime);
  }
  .brand-name {
    margin: 0;
    color: var(--lime);
    font-size: 54px;
    font-weight: 700;
    line-height: 1;
    letter-spacing: 0.5px;
  }
  .name-band {
    position: absolute;
    left: 0;
    top: 312px;
    width: 900px;
    height: 71px;
    background: var(--band);
    display: flex;
    justify-content: center;
    align-items: center;
    color: var(--lime);
  }
  .person-name {
    font-size: 31px;
    font-weight: 700;
  }
  .person-role {
    font-size: 26px;
    font-weight: 400;
    margin-left: 8px;
    padding-top: 4px;
  }
  .accent-block {
    position: absolute;
    left: 914px;
    top: 312px;
    width: 136px;
    height: 71px;
    background: var(--lime);
  }
  .contacts {
    position: absolute;
    left: 103px;
    top: 443px;
    margin: 0;
    padding: 0;
    list-style: none;
    color: var(--white);
    font-size: 26px;
  }
  .contacts li {
    display: flex;
    align-items: center;
    height: 43px;
  }
  .contacts svg {
    width: 22px;
    height: 22px;
    margin-right: 11px;
    flex: none;
  }
  .services {
    position: absolute;
    left: 593px;
    top: 442px;
    margin: 0;
    padding: 0;
    list-style: none;
    color: var(--white);
    font-size: 30px;
  }
  .services li {
    display: flex;
    align-items: center;
    height: 40px;
  }
  .services li::before {
    content: "";
    width: 9px;
    height: 9px;
    background: var(--white);
    margin-right: 11px;
    flex: none;
  }
</style>
</head>
<body>
<div class="canvas">
  <div class="card">
    <div class="brand">
      <span class="brand-dot"></span>
      <h1 class="brand-name">Bright Volley Tennis</h1>
    </div>

    <div class="name-band">
      <span class="person-name">Owen Whitby,</span>
      <span class="person-role">Managing Director</span>
    </div>
    <div class="accent-block"></div>

    <ul class="contacts">
      <li>
        <svg viewBox="0 0 24 24" aria-hidden="true"><path fill="#b5d334" d="M3 9c0-3 4-5 9-5s9 2 9 5v2h-5V8.5c-2-.7-6-.7-8 0V11H3zM6 12h12l2 8H4z"/><circle cx="12" cy="16" r="2" fill="#000"/></svg>
        0491 726 305
      </li>
      <li>
        <svg viewBox="0 0 24 24" aria-hidden="true"><rect x="2" y="6" width="20" height="13" fill="none" stroke="#b5d334" stroke-width="2" transform="rotate(-10 12 12)"/><path d="M3 7l9 6 9-7" fill="none" stroke="#b5d334" stroke-width="2" transform="rotate(-10 12 12)"/></svg>
        brightvolleyracquets@mailbox.example
      </li>
      <li>
        <svg viewBox="0 0 24 24" aria-hidden="true"><circle cx="12" cy="12" r="9" fill="#b5d334"/><path d="M3 12h18M12 3v18M6 6c4 3 8 3 12 0M6 18c4-3 8-3 12 0" fill="none" stroke="#000" stroke-width="1.3"/></svg>
        www.brightvolleyracquets.com.au
      </li>
    </ul>

    <ul class="services">
      <li>Racquet Restringing</li>
      <li>Tennis Strings</li>
      <li>Accessories</li>
    </ul>
  </div>
</div>
</body>
</html>
```